Property Portal needs Chatterloop Cover Image and Sponsor Ad Design

WHO WE ARE
Hi Pitchers! We are an advertising portal that focus on presenting the latest property launches in Singapore. Our platform and interface will provide consumer an enjoyable and easy browsing experience looking for their ideal property to buy/invest, while ensuring updated information, images/videos, and other useful description is provided on each project.

WHAT WE NEED
Our website is www.brightkeyhomes.sg, and we need designs for our Chatterloop page www.facebook.com/brightkeyhomes. One as the Cover Image (815 x 315), and one as our Sponsor Ad Image (1200 x 627). The 2 designs can be similar or different.

DESIGN
We want to convey a professional and sociable feel. A "cool" and elegant design may be suitable, although feel free to have your own look & feel as long as it suits our purpose. Try to have a focus, and not look messy. We don't want to look cheap, spammy or boring in any sense. Be creative and purposeful =) You may use the snapvault images attached or you can use your own. Add symbols or graphics if it helps to give the design a better feel.

For your reference, I find there is a number of good designs with nice look & feel in this project including those withdraw/eliminated.
http://chatterloop.pitchmart.example/contest.aspx?id=218907&page=2
http://chatterloop.pitchmart.example/contest.aspx?id=218907

IDEAS
You may want to embed our portal in an SLATEX device as part of the design (see samples below but replace callpod with SlateX). And/or you can have a blur-out image background to have a focus on what you want to show. Please note that we are not restricting any other designs concept, this is just an idea I have.

CAPTIONS
You may use one or a few of the sample captions below.
- Singapore Latest Property Launches In One Portal (slight emphasis on "in one portal")
- Latest Projects • Updated Info • Best Pricing
- Residential • Commercial • Overseas (perhaps label on images)

Hope we can find an ideal design here. We will request from pitchmart to increase the project budget to give out more participation payments if there is a few good ones. We are also looking to find suitable designers for our future projects as we need a few more designs. If you have questions, feel free to ask me and I will reply promptly.

Reason: Project cancelled and relaunch with different purpose, moved from Newsletter to Chatterloop Design.

IDEAS (UPDATED) I am thinking one way to showcase our portal is perhaps to have our website embedded in an slatex and/or notebook pro device as part of the design. I've attached some designs I came across to show what I mean (only the embedding part). If you are going to do it this way, you can use our main page www.brightkeyhomes.sg and/or a project page www.brightkeyhomes.sg/willowcrest-at-ambergate to display

Target Market(s)

Real Estate Agents, Investors, Developers, General public age 30 & above

Industry/Entity Type

Advertising

Colors
9ccb3b
00a98f
0592cd
3176b5
ffcf3e
5c5c5c

Requirements
Should not have
• I prefer not to use real people stock images unless you are very sure it will work out well.

```html
<!DOCTYPE html>
<html lang="en">
<head>
<meta charset="utf-8">
<title>Singapore Latest Property Launches In One Portal</title>
<link rel="stylesheet" href="https://fonts.googleapis.com/css2?family=Oswald:wght@400;500&family=PT+Serif&family=Open+Sans:wght@400;700&display=swap">
<style>
  :root {
    --brand-green: #8cc63f;
    --brand-green-dark: #5fa52b;
    --white: #ffffff;
    --ink: #333333;
    --ink-soft: #555555;
    --bezel: #161616;
    --bezel-edge: #3a3a3a;
    --dusk-top: #7a6a9c;
    --dusk-mid: #4b4163;
    --dusk-low: #2a2630;
    --pool: #1e4a5c;
    --warm-light: rgba(232, 178, 92, 0.55);
  }
  * { margin: 0; padding: 0; box-sizing: border-box; }
  html, body { width: 1200px; height: 627px; overflow: hidden; background: var(--dusk-low); }
  .ad {
    position: relative;
    width: 1200px;
    height: 627px;
    overflow: hidden;
    font-family: "Open Sans", Arial, sans-serif;
  }
  .scene {
    position: absolute;
    inset: 0;
    background:
      radial-gradient(ellipse 420px 320px at 300px 230px, var(--warm-light), transparent 70%),
      radial-gradient(ellipse 300px 220px at 720px 260px, rgba(220, 170, 90, 0.35), transparent 70%),
      linear-gradient(180deg, transparent 72%, var(--pool) 100%),
      linear-gradient(100deg, #3b3128 0%, #4a3c36 35%, var(--dusk-mid) 62%, var(--dusk-top) 100%);
  }
  .headline {
    position: absolute;
    left: 145px;
    top: 314px;
    color: var(--white);
    font-family: "Oswald", "Arial Narrow", sans-serif;
    font-weight: 400;
    font-size: 33px;
    line-height: 46px;
    text-shadow: 0 1px 4px rgba(0,0,0,0.5);
  }
  .headline-line { display: block; }
  .headline-accent {
    display: inline-block;
    margin-left: 18px;
    padding: 0 14px;
    height: 40px;
    line-height: 40px;
    background: var(--brand-green);
    text-shadow: none;
  }
  .slate {
    position: absolute;
    left: 712px;
    top: 333px;
    width: 352px;
    height: 240px;
    background: var(--bezel);
    border: 2px solid var(--bezel-edge);
    border-radius: 20px;
  }
  .slate-screen {
    position: absolute;
    left: 27px;
    top: 21px;
    width: 268px;
    height: 190px;
    background: var(--white);
    overflow: hidden;
  }
  .portal-brand {
    display: flex;
    flex-direction: column;
    align-items: center;
    margin-top: 12px;
  }
  .portal-name {
    display: flex;
    align-items: center;
    gap: 4px;
    color: var(--brand-green);
    font-weight: 700;
    font-size: 17px;
    line-height: 20px;
  }
  .portal-dot {
    width: 12px; height: 12px;
    border-radius: 50%;
    background: var(--brand-green);
  }
  .portal-tagline {
    font-size: 4px;
    letter-spacing: 0.5px;
    color: var(--ink-soft);
  }
  .listing {
    position: absolute;
    left: 10px;
    top: 59px;
    right: 8px;
    display: flex;
    gap: 8px;
  }
  .listing-photo {
    position: relative;
    flex: 0 0 118px;
    height: 103px;
    background: linear-gradient(180deg, #6a5a7c 0%, #8a6f5a 45%, #2b5466 100%);
  }
  .listing-price {
    position: absolute;
    left: 14px;
    bottom: -10px;
    width: 94px;
    height: 19px;
    border-radius: 4px;
    background: linear-gradient(180deg, var(--brand-green), var(--brand-green-dark));
    color: var(--white);
    font-size: 10px;
    font-weight: 700;
    text-align: center;
    line-height: 19px;
  }
  .listing-info { flex: 1; color: var(--ink); }
  .listing-title {
    font-family: "PT Serif", Georgia, serif;
    font-size: 11px;
    padding-bottom: 4px;
    margin-bottom: 6px;
    border-bottom: 1px solid #e2e2e2;
  }
  .listing-facts, .listing-update {
    font-size: 4.6px;
    font-weight: 700;
    line-height: 7.6px;
  }
  .listing-update { margin-top: 6px; }
</style>
</head>
<body>
<main class="ad">
  <div class="scene" role="img" aria-label="Photo of a modern condominium at dusk with lit balconies, palm trees and a pool, and two hands holding a tablet"></div>

  <h1 class="headline">
    <span class="headline-line">Singapore Latest Property</span>
    <span class="headline-line">Launches<span class="headline-accent">In One Portal</span></span>
  </h1>

  <div class="slate">
    <div class="slate-screen">
      <div class="portal-brand">
        <div class="portal-name"><span class="portal-dot"></span>brightkeyhomes.sg</div>
        <div class="portal-tagline">BROWSE THE LATEST PROPERTY LAUNCHES TODAY</div>
      </div>
      <div class="listing">
        <div class="listing-photo" role="img" aria-label="Photo of the condominium project at dusk">
          <div class="listing-price">$2,900,000++</div>
        </div>
        <div class="listing-info">
          <div class="listing-title">Willowcrest Villas</div>
          <div class="listing-facts">
            Type : Cluster House<br>
            District : 20 (Ang Mo Kio) &nbsp;&nbsp; Tenure : Freehold<br>
            Status : Official Launch &nbsp;&nbsp; Avg Price : $7xx-9xxpsf<br>
            Total Units : 118 (3520-4026sqft)
          </div>
          <div class="listing-update">
            Latest Update : Special discount available for Star Buy Units! Check below for more details
          </div>
        </div>
      </div>
    </div>
  </div>
</main>
</body>
</html>
```